Label design - Superfood blend

We are a family owned nutrition company with big ambitions. Our goal is to develop a range of 100% natural supplements for women, inspired by nature & modern technology that helps them meet their nutritional needs while nourishing them from within. All our products are junk free because we believe that that’s how nature intended it. We also produce products through a sustainable process and only use biodegradable packaging for our products (See link - https://www.loamwrap.org.uk/biodegradable-stand-pouch-250g-kraft)

Our brand style is modern and minimalist. This same style will be reflected in our social media, website and we want it to be represented through the label designs for our product packaging.

We want some creative designers to design a label that is true to our style (See attached packaging brief with designs we like) and displays our values of Premium, High Quality, Organic Real Food supplements focused on women. I have provided examples in the attached brief, but please only use as inspiration, I dont want any of them to be copied (sorry have had my fingers burnt already !)
Updates

Hello all, Please note this design is for a LABEL and not the whole package. We will have a 500gm biodegradable brown package, and we will have a label (which is what this project is about) that will be stuck on the front. The size of the label will be a rectangle (unless you come up with a new shape) in the size 20cm * 15cm. Please do not submit designs for the WHOLE from of the package, as we dont intend to have printed packages. Regards

Hello all, I have added a new logo version to the attachments, could you please also try that version. Could you also please look at the new sliders. We are only looking for a minimlaist theme. If you dont know what that means, please do feel free to ask, I would be happy to supply examples. Minimalist designs, means clean, modern, upmarket, elegant designs. It does not use too many colors and mostly sticks to a combination of black and white with colors used sparingly. See some below for your reference anyway. https://www.pitchloft.co.uk/design/13359317 https://www.pitchloft.co.uk/design/17270649 https://www.pitchloft.co.uk/design/12584145 https://www.pitchloft.co.uk/design/12367479 https://www.snapquilt.com/search/pins/?q=minimalist%20label%20design&rs=rs&eq=&etslf=2809&term_meta[]=minimalist%7Crecentsearch%7Cundefined&term_meta[]=label%7Crecentsearch%7Cundefined&term_meta[]=design%7Crecentsearch%7Cundefined Regards

Target Market(s)

The target market is women between the age 25 to 45, based in UK (mostly based in larger cities in UK). They are typically middle class or higher and would be in demanding jobs and social lives, that requires for them to meet their nutrition needs in convenient, easy to take forms. The women would also be socially conscious and sensitive to issues like women's rights, environmental issues, healthy food, organic food and sustainability etc. I have a much more detailed customer avatar if required

Font styles to use
Serif
Sans Serif
Decorative
Script

Colors
e8e8e8
474747
1b1b1b
add136

Requirements
Must have
• The label, should look minimalist and modern, throw in some out of the box creativity and we have a winner. Creativity will definitely be of importance. Our packaging is a biodegradable brown paper stand up pouch (Example link in product description). So to make it standout from other colorful packaging - being creative would definitely help.
• Please use the color schemes provided in the brief (See attachments). But if you want to experiment I would be open to it, as long as they are still minimalist and does not stray very far from the color given in the brief :)

```html
<!DOCTYPE html>
<html lang="en">
<head>
<meta charset="utf-8">
<title>Rooted Well – Label</title>
<link rel="stylesheet" href="https://fonts.googleapis.com/css2?family=Lexend:wght@400;500&family=Montserrat:wght@400;500&display=swap">
<style>
  :root {
    --page: #f4f4f4;
    --label: #ffffff;
    --ink: #1b1b1b;
    --grey: #474747;
    --soft: #e8e8e8;
    --accent: #add136;
    --accent-band: #bcd884;
  }
  html, body {
    margin: 0;
    width: 1200px;
    height: 1200px;
    overflow: hidden;
    background: var(--page);
  }
  .canvas {
    position: relative;
    width: 1200px;
    height: 1200px;
  }
  .label {
    position: absolute;
    left: 212px;
    top: 78px;
    width: 776px;
    height: 1045px;
    background: linear-gradient(180deg, #f7f7f7 0%, var(--label) 45%, #f9f9f9 100%);
    border-radius: 26px;
    box-shadow: 0 2px 10px rgba(0,0,0,0.08);
    overflow: hidden;
    font-family: "Montserrat", sans-serif;
    color: var(--grey);
  }
  .brand {
    position: absolute;
    left: 259px;
    top: 97px;
    width: 258px;
    height: 258px;
    border: 2px solid var(--grey);
    border-radius: 50%;
    box-sizing: border-box;
    display: flex;
    align-items: center;
    justify-content: center;
  }
  .brand-name {
    font-family: "Montserrat", sans-serif;
    font-weight: 500;
    font-size: 27px;
    letter-spacing: 5px;
    color: var(--ink);
    margin-right: -5px;
  }
  .band {
    position: absolute;
    left: 0;
    top: 459px;
    width: 100%;
    height: 121px;
    background: var(--accent-band);
  }
  .title-frame {
    position: absolute;
    left: 140px;
    top: 404px;
    width: 504px;
    height: 231px;
    border: 3px solid var(--ink);
    box-sizing: border-box;
  }
  .title {
    position: absolute;
    left: 0;
    top: 478px;
    width: 100%;
    margin: 0;
    text-align: center;
    font-family: "Lexend", sans-serif;
    font-weight: 500;
    font-size: 58px;
    line-height: 84px;
    color: var(--ink);
    letter-spacing: 0.5px;
  }
  .tag {
    position: absolute;
    left: 253px;
    top: 613px;
    width: 286px;
    height: 55px;
    background: var(--ink);
    color: #ffffff;
    font-size: 21px;
    font-weight: 500;
    letter-spacing: 0.5px;
    display: flex;
    align-items: center;
    justify-content: center;
  }
  .description {
    position: absolute;
    left: 0;
    top: 728px;
    width: 100%;
    margin: 0;
    text-align: center;
    font-size: 27px;
    line-height: 36px;
    color: var(--grey);
  }
  .badges {
    position: absolute;
    left: 0;
    top: 849px;
    width: 100%;
    height: 92px;
  }
  .net-weight-rule {
    position: absolute;
    left: 66px;
    top: 982px;
    width: 654px;
    height: 2px;
  }
  .net-weight {
    position: absolute;
    left: 0;
    top: 970px;
    width: 100%;
    text-align: center;
    font-size: 23px;
    line-height: 30px;
    color: var(--grey);
  }
</style>
</head>
<body>
<main class="canvas">
  <section class="label">
    <div class="brand"><span class="brand-name">VERDALIA</span></div>

    <div class="band"></div>
    <div class="title-frame"></div>
    <h1 class="title">ROOTED WELL</h1>
    <div class="tag">FOOD SUPPLEMENT</div>

    <p class="description">Organic, Plant-Based Prebiotics<br>and Superfood Blend</p>

    <svg class="badges" viewBox="0 0 776 92" aria-hidden="true">
      <circle cx="319" cy="46" r="40" fill="none" stroke="var(--grey)" stroke-width="3"/>
      <circle cx="470" cy="46" r="40" fill="var(--ink)"/>
    </svg>

    <svg class="net-weight-rule" viewBox="0 0 654 2" aria-hidden="true">
      <line x1="0" y1="1" x2="238" y2="1" stroke="var(--grey)" stroke-width="2"/>
      <line x1="406" y1="1" x2="654" y2="1" stroke="var(--grey)" stroke-width="2"/>
    </svg>
    <div class="net-weight">Net Weight<br>500 g</div>
  </section>
</main>
</body>
</html>
```